Redesign of business card for Cedar Ridge Mechanical

We are looking for a new design for our business cards for Cedar Ridge Mechanical. We are a plumbing & HVAC construction company, operating on the West Coast of Canada and USA. Logo attached.
Industry/Entity Type
Construction - Plumbing & HVAC
Contact Information for Business Card
Name, address, phone numbers, email, website address
Look and feel
Each slider illustrates characteristics of the customer's brand and the style your logo design should communicate.

```html
<!DOCTYPE html>
<html lang="en">
<head>
<meta charset="utf-8">
<title>Cedar Ridge Mechanical – Business Card</title>
<link href="https://fonts.googleapis.com/css2?family=Lato:wght@400;700&family=Montserrat:wght@500;700&display=swap" rel="stylesheet">
<style>
  :root {
    --backdrop: #2b2c2e;
    --card-white: #ffffff;
    --card-black: #232325;
    --ink: #1e1e1f;
    --ink-soft: #6b6b6d;
    --rule-grey: #a9a9ab;
    --paper-text: #ffffff;
  }
  * { margin: 0; padding: 0; box-sizing: border-box; }
  html, body {
    width: 1200px; height: 952px; overflow: hidden;
    background: var(--backdrop);
  }
  .canvas { position: relative; width: 1200px; height: 952px; }

  .card {
    position: absolute; left: 300px;
    width: 600px; height: 343px;
    box-shadow: 0 8px 24px rgba(0,0,0,.35);
  }

  /* Front: white contact side */
  .card--front { top: 100px; background: var(--card-white); }
  .brand {
    position: absolute; left: 48px; top: 128px; width: 210px;
    display: flex; align-items: center; gap: 12px;
  }
  .brand__square {
    flex: none; width: 26px; height: 26px; background: var(--ink);
  }
  .brand__name {
    font-family: "Lato", sans-serif; font-weight: 700;
    font-size: 20px; line-height: 1.15; letter-spacing: .06em;
    text-transform: uppercase; color: var(--ink);
  }
  .divider-top {
    position: absolute; left: 290px; top: 0; width: 2px; height: 170px;
    background: var(--rule-grey);
  }
  .divider-bottom {
    position: absolute; left: 289px; top: 176px; width: 5px; height: 167px;
    background: var(--ink);
  }
  .contact {
    position: absolute; left: 322px; top: 70px; width: 260px;
    font-family: "Lato", sans-serif; color: var(--ink-soft);
  }
  .contact__name {
    font-family: "Montserrat", sans-serif; font-weight: 500;
    font-size: 19px; letter-spacing: .04em; color: var(--ink);
    text-transform: uppercase;
  }
  .contact__name strong { font-weight: 700; }
  .contact__title { font-size: 14px; margin-top: 2px; }
  .contact__rule {
    width: 56px; height: 1px; background: var(--rule-grey); margin: 8px 0 14px;
  }
  .contact__row {
    display: flex; align-items: flex-start; gap: 10px;
    font-size: 13px; line-height: 1.35; margin-bottom: 7px;
  }
  .contact__icon {
    flex: none; width: 16px; height: 16px; border-radius: 3px;
    background: var(--ink); display: flex; align-items: center; justify-content: center;
    margin-top: 1px;
  }
  .contact__icon svg { width: 10px; height: 10px; fill: #fff; }

  /* Back: black brand side */
  .card--back { top: 500px; background: var(--card-black); }
  .card--back .brand {
    left: 50%; top: 50%; transform: translate(-50%, -50%); width: auto;
  }
  .card--back .brand__square { background: var(--paper-text); }
  .card--back .brand__name { color: var(--paper-text); font-size: 24px; white-space: nowrap; }
</style>
</head>
<body>
<main class="canvas">

  <section class="card card--front" aria-label="Business card front">
    <div class="brand">
      <span class="brand__square"></span>
      <span class="brand__name">Cedar Ridge<br>Mechanical</span>
    </div>

    <div class="divider-top"></div>
    <div class="divider-bottom"></div>

    <div class="contact">
      <p class="contact__name">Daniel R. <strong>Hartwell</strong></p>
      <p class="contact__title">Managing Director</p>
      <div class="contact__rule"></div>

      <div class="contact__row">
        <span class="contact__icon"><svg viewBox="0 0 10 10"><path d="M5 0a3.5 3.5 0 0 0-3.5 3.5C1.5 6 5 10 5 10s3.5-4 3.5-6.5A3.5 3.5 0 0 0 5 0zm0 5a1.4 1.4 0 1 1 0-2.8A1.4 1.4 0 0 1 5 5z"/></svg></span>
        <span>1720 Harbor View Road<br>Portland, OR 97209</span>
      </div>
      <div class="contact__row">
        <span class="contact__icon"><svg viewBox="0 0 10 10"><path d="M2 0l2 2.3-1.1 1.3a6 6 0 0 0 3.5 3.5L7.7 6 10 8l-1.2 1.6C4.5 10 0 5.5.4 1.2z"/></svg></span>
        <span>+00 987 654 32</span>
      </div>
      <div class="contact__row">
        <span class="contact__icon"><svg viewBox="0 0 10 10"><path d="M0 2h10v6H0zM0 2l5 3.5L10 2" stroke="#232325" stroke-width=".8"/></svg></span>
        <span>office@cedarridgemech.com</span>
      </div>
      <div class="contact__row">
        <span class="contact__icon"><svg viewBox="0 0 10 10"><path d="M1 1l8 3.5-3.2 1.1L4.5 9z"/></svg></span>
        <span>www.cedarridgemech.com</span>
      </div>
    </div>
  </section>

  <section class="card card--back" aria-label="Business card back">
    <div class="brand">
      <span class="brand__square"></span>
      <span class="brand__name">Cedar Ridge Mechanical</span>
    </div>
  </section>

</main>
</body>
</html>
```